Website for Dental Office - The Bright Arch Clinic

The bright arch clinic is a dental office offering cosmetic dentistry, general dentistry, and multi-specialty dental care all under one roof in our state-of-the-art cosmetic dental center. We are particularly striving to provide services that fit the need of the young generation. Thus, we hope to have a modern, professional concise website that represents our spirit.

*Should be able to switch from English to Chinese

6 sections besides homepage:
Home, Meet us, Services,
Patient Info, Cases&Reviews, Blog, Contact

The Services sections should contain multiple subsections such as cleaning and prevention, cosmetic dentistry, implant dentistry, removable dentures, etc...
The Patient Info section is also intended to contain several subsections such as
New Patient offer, accepted Insurance, patient portal, helpful tips, etc...

Target Market(s)

young generation

Coding

Coded - Design and coding required

Number of Pages Required

5+ page

Font styles to use
Sans Serif

Colors
0592cd
33a6d7
85cae6
00a990
33b8a4
86cfc6
cee9f5
cfeae6
3277b5

Requirements
Must have
• *Should be able to switch from English to Chinese
Nice to have
• http://www.thebrightarchclinic.com/
• As a reference, the above link is the current website, but we would like to change the appearance and the content (our new logo's picture is attached)

```html
<!DOCTYPE html>
<html lang="en">
<head>
<meta charset="utf-8">
<title>New Patient Offers – The Bright Arch Clinic</title>
<link rel="stylesheet" href="https://fonts.googleapis.com/css2?family=Montserrat:wght@400;500;600;700;800&display=swap">
<style>
:root{
  --blue:#0592cd;
  --blue-mid:#33a6d7;
  --blue-light:#85cae6;
  --blue-pale:#cee9f5;
  --green:#00a990;
  --green-mid:#33b8a4;
  --navy:#3277b5;
  --ink:#111;
  --text:#555;
  --footer-bg:#f2f2f2;
  --footer-bar:#ebebeb;
}
*{margin:0;padding:0;box-sizing:border-box}
html,body{width:704px;height:1200px;overflow:hidden}
body{position:relative;font-family:'Montserrat',sans-serif;color:var(--text);
  background:linear-gradient(#d9effb 60px,#f3fafe 230px,#fff 450px);}
.abs{position:absolute}
.top-line{left:0;top:0;width:704px;height:1.5px;background:var(--navy);z-index:3}
.header-curve{left:0;top:0;z-index:1}
.brand{left:95px;top:12px;display:flex;align-items:center;gap:6px;z-index:2}
.brand-mark{width:22px;height:22px;background:var(--blue-mid);border-radius:3px}
.brand-name{font-size:11px;font-weight:700;color:var(--blue-mid);line-height:1.1;width:76px}
.nav{left:233px;top:23px;display:flex;gap:11px;font-size:6.2px;font-weight:500;color:#555;z-index:2}
.nav .active{color:var(--green)}
.phone-bubble{left:507px;top:-9px;width:66px;height:66px;border-radius:50%;background:var(--navy);z-index:2;
  color:#fff;font-size:7.4px;font-weight:700;text-align:center;padding-top:18px}
.phone-bubble svg{display:block;margin:0 auto 3px}
.lang{left:580px;top:17px;width:29px;height:17px;border-radius:2px;background:var(--green);z-index:2;
  color:#fff;font-size:5.6px;display:flex;align-items:center;justify-content:center;gap:2px}
.page-title{left:0;width:704px;top:139px;text-align:center;font-size:26px;font-weight:800;color:var(--ink);letter-spacing:.3px}
.intro{left:130px;width:444px;top:179px;text-align:center;font-size:6.7px;line-height:11.4px}
.photo{position:absolute}
.offer-eyebrow{font-size:7px;font-weight:700;color:#fff}
.offer-discount{font-size:16px;font-weight:700;color:#fff}
.offer-title{font-size:12.3px;font-weight:400;color:#fff}
.offer-text{font-size:6.4px;line-height:11.4px;color:#fff}
.btn{position:absolute;background:#fff;border-radius:14px;color:var(--ink);font-size:7.3px;font-weight:700;
  display:flex;align-items:center;justify-content:center;width:132px;height:26px}
.offer-circle{left:116px;top:227px;width:220px;height:220px;border-radius:50%;background:var(--blue);text-align:center}
.panel{position:absolute;width:257px;height:185px}
.panel-green{left:352px;top:483px;background:var(--green)}
.panel-navy{left:95px;top:703px;background:var(--navy)}
.footer{left:0;top:985px;width:704px;height:215px;background:var(--footer-bg)}
.footer-bar{left:0;top:1174px;width:704px;height:26px;background:var(--footer-bar);font-size:6.2px;color:#999}
.cta{left:95px;top:937px}
.cta-small{left:108px;top:970px;font-size:6.8px;color:#fff}
.cta-big{left:108px;top:981px;font-size:21px;font-weight:800;color:#fff;letter-spacing:.3px}
.col-title{font-size:7px;font-weight:700;color:#333}
.col-list{font-size:6.2px;line-height:11px;color:#555;list-style:none}
.hours td{font-size:6.2px;height:11px;padding:0;color:#555;vertical-align:top}
.hours td.t{font-weight:700;color:#333;padding-left:5px}
.foot-brand{left:95px;top:1062px;width:115px;text-align:center}
.foot-mark{width:34px;height:34px;border-radius:4px;background:var(--blue-light);margin:0 auto 6px}
.foot-name{font-size:10.5px;font-weight:700;color:var(--blue-mid)}
.social{width:20px;height:20px;border-radius:50%}
.contact-line{font-size:6.2px;line-height:11px;color:#555}
</style>
</head>
<body>
<div class="abs top-line"></div>
<svg class="abs header-curve" width="704" height="100" viewBox="0 0 704 100"><path d="M0 0H704V38Q352 138 0 38Z" fill="#fff"/></svg>

<div class="abs brand"><div class="brand-mark"></div><div class="brand-name">THE BRIGHT ARCH CLINIC</div></div>
<nav class="abs nav"><span>HOME</span><span>MEET US</span><span>SERVICES</span><span class="active">PATIENT INFO</span><span>REVIEWS</span><span>BLOG</span><span>CONTACT</span></nav>
<div class="abs phone-bubble">
  <svg width="13" height="13" viewBox="0 0 24 24"><path fill="#fff" d="M6.6 10.8c1.4 2.8 3.8 5.1 6.6 6.6l2.2-2.2c.3-.3.7-.4 1-.2 1.1.4 2.3.6 3.6.6.6 0 1 .4 1 1V20c0 .6-.4 1-1 1C10.6 21 3 13.4 3 4c0-.6.4-1 1-1h3.5c.6 0 1 .4 1 1 0 1.3.2 2.5.6 3.6.1.3 0 .7-.2 1z"/></svg>
  555.214.7080
</div>
<div class="abs lang">汉语 <svg width="5" height="4" viewBox="0 0 10 6"><path d="M1 1l4 4 4-4" stroke="#fff" stroke-width="1.6" fill="none"/></svg></div>

<h1 class="abs page-title">NEW PATIENT OFFERS</h1>
<p class="abs intro">Lorem Ipsum is simply dummy text of the printing and typesetting industry. Lorem Ipsum has been the industry's standard dummy text ever since the 1500s, when an unknown printer took a galley.</p>

<!-- Offer 1 -->
<div class="photo" role="img" aria-label="Photo of three young women laughing together outdoors" style="left:95px;top:254px;width:514px;height:176px;background:linear-gradient(90deg,#a89486 0%,#6f8a86 45%,#8aa8bf 70%,#c07a52 100%)"></div>
<div class="abs offer-circle">
  <div class="offer-eyebrow" style="margin-top:42px">GET YOUR SUMMER SMILE</div>
  <div class="offer-discount" style="margin-top:5px">50% OFF</div>
  <div class="offer-title" style="margin-top:6px">IN-OFFICE TEETH WHITENING</div>
  <p class="offer-text" style="margin:8px 24px 0">Lorem Ipsum is simply dummy text of the printing and typesetting industry. Lorem Ipsum has been the industry's standard dummy text ever since the 1500s, when an unknown printer took a galley.</p>
</div>
<a class="btn" style="left:161px;top:387px">BOOK AN APPOINTMENT</a>

<!-- Offer 2 -->
<div class="photo" role="img" aria-label="Photo of a smiling little girl with curly hair" style="left:95px;top:483px;width:257px;height:185px;background:linear-gradient(90deg,#e8e2dc,#d9c2b0 40%,#f0eeec)"></div>
<div class="panel panel-green">
  <div class="offer-eyebrow abs" style="left:21px;top:26px">GET YOUR SUMMER SMILE</div>
  <div class="offer-discount abs" style="left:21px;top:46px">50% OFF</div>
  <div class="offer-title abs" style="left:21px;top:72px">IN-OFFICE TEETH WHITENING</div>
  <p class="offer-text abs" style="left:21px;top:92px;width:200px">Lorem Ipsum is simply dummy text of the printing and typesetting industry. Lorem Ipsum has been the industry's standard dummy text ever since the 1500.</p>
</div>
<a class="btn" style="left:372px;top:618px">BOOK AN APPOINTMENT</a>

<!-- Offer 3 -->
<div class="panel panel-navy">
  <div class="offer-eyebrow abs" style="left:27px;top:24px">GET YOUR SUMMER SMILE</div>
  <div class="offer-discount abs" style="left:27px;top:45px">50% OFF</div>
  <div class="offer-title abs" style="left:27px;top:71px">IN-OFFICE TEETH WHITENING</div>
  <p class="offer-text abs" style="left:27px;top:90px;width:200px">Lorem Ipsum is simply dummy text of the printing and typesetting industry. Lorem Ipsum has been the industry's standard dummy text ever since the 1500.</p>
</div>
<a class="btn" style="left:121px;top:836px">BOOK AN APPOINTMENT</a>
<div class="photo" role="img" aria-label="Photo of a smiling young couple in sunglasses by the sea" style="left:352px;top:703px;width:257px;height:185px;background:linear-gradient(90deg,#c9d3d8,#b79878 45%,#7a5a46 75%,#c9c4bd)"></div>

<!-- Footer -->
<div class="abs footer"></div>
<svg class="abs cta" width="514" height="98" viewBox="0 0 514 98">
  <defs><linearGradient id="ctaGrad" x1="0" x2="1" y1="0" y2="0"><stop offset="0" stop-color="#0592cd"/><stop offset="1" stop-color="#00a990"/></linearGradient></defs>
  <path d="M4 0L510 26Q514 26.3 514 30V93Q514 97 510 97H4Q0 97 0 93V4Q0 0 4 0Z" fill="url(#ctaGrad)"/>
</svg>
<div class="abs cta-small">Lorem Ipsum is dummy text of the printing and typesetting.</div>
<div class="abs cta-big">YOUR SMILE. OUR PASSION.</div>
<a class="btn" style="left:459px;top:984px">BOOK AN APPOINTMENT</a>

<div class="abs foot-brand"><div class="foot-mark"></div><div class="foot-name">THE BRIGHT ARCH CLINIC</div></div>
<div class="abs social" style="left:106px;top:1128px;background:#1da1f2"></div>
<div class="abs social" style="left:130px;top:1128px;background:#3b5998"></div>
<div class="abs social" style="left:154px;top:1128px;background:var(--green)"></div>
<div class="abs social" style="left:179px;top:1128px;background:var(--green-mid)"></div>

<div class="abs" style="left:229px;top:1060px">
  <div class="col-title">USEFUL LINKS</div>
  <ul class="col-list" style="margin-top:6px"><li>Home</li><li>Meet Us</li><li>Services</li><li>Patient Info</li><li>Case &amp; Reviews</li><li>Blog</li><li>Contact</li></ul>
</div>
<div class="abs" style="left:362px;top:1060px">
  <div class="col-title">OPENING HOURS</div>
  <table class="hours" style="margin-top:6px;border-collapse:collapse">
    <tr><td>Sunday &amp; Monday</td><td class="t">Closed</td></tr>
    <tr><td>Tuesday</td><td class="t">9:30AM – 5:00PM</td></tr>
    <tr><td>Wednesday</td><td class="t">Closed</td></tr>
    <tr><td>Thursday</td><td class="t">9:30AM – 5:00PM</td></tr>
    <tr><td>Friday</td><td class="t">9:00AM – 5:00PM</td></tr>
    <tr><td>Saturday</td><td class="t">9:00AM – 5:00PM</td></tr>
  </table>
</div>
<div class="abs" style="left:496px;top:1060px">
  <div class="col-title">CONTACT INFO</div>
  <svg class="abs" style="left:0;top:18px" width="7" height="9" viewBox="0 0 10 14"><path fill="var(--green)" d="M5 0a5 5 0 0 0-5 5c0 4 5 9 5 9s5-5 5-9a5 5 0 0 0-5-5zm0 7a2 2 0 1 1 0-4 2 2 0 0 1 0 4z"/></svg>
  <div class="abs contact-line" style="left:13px;top:15px;width:100px">27 Harbor Lane, Suite 12, Millbrook MA 02111</div>
  <svg class="abs" style="left:0;top:46px" width="8" height="8" viewBox="0 0 24 24"><path fill="var(--navy)" d="M6.6 10.8c1.4 2.8 3.8 5.1 6.6 6.6l2.2-2.2c.3-.3.7-.4 1-.2 1.1.4 2.3.6 3.6.6.6 0 1 .4 1 1V20c0 .6-.4 1-1 1C10.6 21 3 13.4 3 4c0-.6.4-1 1-1h3.5c.6 0 1 .4 1 1 0 1.3.2 2.5.6 3.6.1.3 0 .7-.2 1z"/></svg>
  <div class="abs" style="left:13px;top:44px;font-size:8.5px;color:#555;white-space:nowrap">555.214.7080</div>
  <svg class="abs" style="left:0;top:67px" width="9" height="7" viewBox="0 0 18 13"><rect width="18" height="13" rx="1" fill="var(--blue-mid)"/><path d="M1 1l8 6 8-6" stroke="#fff" stroke-width="1.4" fill="none"/></svg>
  <div class="abs contact-line" style="left:13px;top:64px;white-space:nowrap">info@thebrightarchclinic.com</div>
</div>

<div class="abs footer-bar">
  <div class="abs" style="left:95px;top:9px">© <span style="color:var(--navy)">The Bright Arch Clinic</span> – 2019. All Rights Reserved.</div>
  <div class="abs" style="right:95px;top:9px;color:var(--green)">Harbor Aesthetic Care</div>
</div>
</body>
</html>
```